Las Vegas transportation company needs a dynamic design for business cards

We are a transportation management company based in Las Vegas specializing in operating and maintaining public transit systems. We want to keep our existing logo but would like to design business cards that feature one or more transit systems (e.g. monorail, train, bus) and maybe also the Las Vegas landscape.

```html
<!DOCTYPE html>
<html lang="en">
<head>
<meta charset="utf-8">
<title>Meridian Transit Group – Business Card</title>
<link rel="stylesheet" href="https://fonts.googleapis.com/css2?family=Cinzel:wght@400;600&family=Arimo:wght@400&display=swap">
<style>
  :root {
    --navy: #14206b;
    --sky: #8fb2e6;
    --ink: #1a1a1a;
    --paper: #ffffff;
    --backdrop: #d6d6d6;
    --divider: #e6e8ee;
    --city-top: #5f7f99;
    --city-bottom: #8c8c92;
    --rail-top: #c39a3c;
    --rail-bottom: #4a4a52;
  }
  * { box-sizing: border-box; margin: 0; padding: 0; }
  html, body {
    width: 1200px; height: 800px; overflow: hidden;
    background: var(--backdrop);
  }
  .stage { position: relative; width: 1200px; height: 800px; }

  .card {
    position: absolute;
    width: 560px; height: 320px;
    background: var(--paper);
    box-shadow: 0 6px 18px rgba(0,0,0,0.18);
    overflow: hidden;
  }
  .card--front { left: 60px; top: 70px; }
  .card--back  { left: 580px; top: 410px; border-bottom: 3px solid var(--navy); }

  /* Front */
  .brand {
    position: absolute; left: 0; top: 0; width: 268px; height: 100%;
    display: flex; align-items: center; justify-content: center;
  }
  .brand__name {
    font-family: "Cinzel", serif; font-weight: 400;
    color: var(--navy); font-size: 28px; line-height: 1.2;
    text-align: center; letter-spacing: 1px;
  }
  .card__divider {
    position: absolute; left: 268px; top: 30px; width: 1px; height: 260px;
    background: var(--divider);
  }
  .contact {
    position: absolute; left: 295px; top: 58px; right: 24px;
    font-family: "Arimo", sans-serif; color: var(--ink);
  }
  .contact__name {
    font-family: "Cinzel", serif; font-weight: 600; color: var(--navy);
    font-size: 24px; letter-spacing: 0.5px; line-height: 1;
  }
  .contact__title { font-size: 15px; margin: 6px 0 18px; }
  .contact__list { list-style: none; }
  .contact__item {
    display: flex; align-items: center; gap: 8px;
    font-size: 14px; line-height: 22px;
  }
  .contact__item svg { width: 13px; height: 13px; flex: none; fill: var(--navy); }
  .contact__web-accent { color: var(--sky); }
  .contact__address { font-size: 14px; line-height: 20px; margin-top: 14px; }

  /* Back */
  .photo { position: absolute; inset: 0; }
  .photo--bus {
    clip-path: polygon(0 0, 40% 0, 56% 100%, 0 100%);
    background: linear-gradient(180deg, var(--city-top) 0%, var(--city-bottom) 100%);
  }
  .photo--train {
    clip-path: polygon(41.5% 0, 100% 0, 100% 100%, 57.5% 100%);
    background: linear-gradient(160deg, var(--rail-top) 0%, var(--rail-bottom) 100%);
  }
</style>
</head>
<body>
<main class="stage">

  <section class="card card--front" aria-label="Business card front">
    <div class="brand">
      <p class="brand__name">Meridian<br>Transit Group</p>
    </div>
    <div class="card__divider"></div>
    <div class="contact">
      <h1 class="contact__name">DANIEL REYES</h1>
      <p class="contact__title">Managing Director</p>
      <ul class="contact__list">
        <li class="contact__item">
          <svg viewBox="0 0 24 24" aria-hidden="true"><path d="M6.6 10.8a15.1 15.1 0 0 0 6.6 6.6l2.2-2.2a1 1 0 0 1 1-.25 11.4 11.4 0 0 0 3.6.57 1 1 0 0 1 1 1V20a1 1 0 0 1-1 1A17 17 0 0 1 3 4a1 1 0 0 1 1-1h3.5a1 1 0 0 1 1 1c0 1.25.2 2.45.57 3.57a1 1 0 0 1-.25 1z"/></svg>
          <span>044-987 654 321</span>
        </li>
        <li class="contact__item">
          <svg viewBox="0 0 24 24" aria-hidden="true"><path d="M2 5h20v14H2zm2 2v.5l8 5 8-5V7zm0 2.8V17h16V9.8l-8 5z"/></svg>
          <span>hello@meridiantransit.com</span>
        </li>
        <li class="contact__item">
          <svg viewBox="0 0 24 24" aria-hidden="true"><path d="M12 2a10 10 0 1 0 0 20 10 10 0 0 0 0-20zm0 2a14 14 0 0 1 1.9 4h-3.8A14 14 0 0 1 12 4zM4.3 14a8.2 8.2 0 0 1 0-4h3.4a16.5 16.5 0 0 0 0 4zm5.4 0a14.7 14.7 0 0 1 0-4h4.6a14.7 14.7 0 0 1 0 4zm6.6 0a16.5 16.5 0 0 0 0-4h3.4a8.2 8.2 0 0 1 0 4zM12 20a14 14 0 0 1-1.9-4h3.8A14 14 0 0 1 12 20z"/></svg>
          <span>www.<span class="contact__web-accent">meridiantransit</span>.com</span>
        </li>
      </ul>
      <p class="contact__address">88 Desert Rail Avenue<br>89101, United States</p>
    </div>
  </section>

  <section class="card card--back" aria-label="Business card back">
    <div class="photo photo--bus" role="img" aria-label="Photo placeholder: red double-decker bus on a city street"></div>
    <div class="photo photo--train" role="img" aria-label="Photo placeholder: yellow and black locomotive among autumn trees"></div>
  </section>

</main>
</body>
</html>
```